Modern Business Card For A Digital Advertising Company

I'll be print on the Pell Prints Velour paper http://us.pellprints.com/products/velour/business-cards.html
Need's to be modern and use the color palette of the logo or gray scales. I think integrating the pixelation of the logo in to the card and having it wrap from one side to the other could be interesting. My company provides ad operations, web development, and number of other services to websites around the world. You can see my website at http://www.zantorhq.com
Contact info on the card needs to have
Owen Lasko
President
p.318.204.6637
owen@zantorhq.com
http://www.zantorhq.com
Doesn't necessarily need to be in that order
Website owners
Business

```html
<!DOCTYPE html>
<html lang="en">
<head>
<meta charset="utf-8">
<title>Zantor Business Card</title>
<link href="https://fonts.googleapis.com/css2?family=PT+Serif:wght@400;700&family=Didact+Gothic&display=swap" rel="stylesheet">
<style>
  :root {
    --stage: #b9b9b9;
    --card-white: #ffffff;
    --brand-green: #7dc242;
    --brand-green-dark: #5e9e2c;
    --charcoal: #3f413d;
    --charcoal-deep: #2a2b28;
    --ink: #4a4a4a;
    --light-text: #e8e8e8;
  }
  * { margin: 0; padding: 0; box-sizing: border-box; }
  html, body { width: 1200px; height: 450px; overflow: hidden; }
  body { background: var(--stage); position: relative; font-family: "PT Serif", Georgia, serif; }

  .card {
    position: absolute; top: 62px; width: 525px; height: 298px;
    border-radius: 22px; overflow: hidden;
  }
  .card-front { left: 58px; background: var(--card-white); }
  .card-back {
    left: 621px;
    background: linear-gradient(90deg, #4b4d49 0%, var(--charcoal) 45%, var(--charcoal-deep) 100%);
  }

  .brand { position: absolute; display: flex; align-items: center; gap: 10px; font-weight: 700; }
  .brand-mark { display: block; }
  .card-front .brand { left: 66px; top: 118px; color: var(--brand-green); font-size: 38px; letter-spacing: 1px; }
  .card-front .brand-mark { width: 20px; height: 20px; background: var(--brand-green); }

  .contact-list { position: absolute; left: 265px; top: 95px; list-style: none; color: var(--ink); font-size: 15px; }
  .contact-list li { display: flex; align-items: center; gap: 5px; height: 21.5px; }
  .contact-icon { width: 11px; height: 11px; flex: none; }

  .footer-wave { position: absolute; left: 0; top: 0; width: 525px; height: 298px; }

  .person { position: absolute; left: 60px; top: 264px; color: #ffffff; }
  .person-name { font-weight: 700; font-size: 18px; }
  .person-title { font-size: 15px; }

  .card-back .brand {
    left: 0; right: 0; top: 88px; justify-content: center;
    color: #ffffff; font-size: 64px; letter-spacing: 3px;
  }
  .card-back .brand-mark { width: 30px; height: 30px; background: #ffffff; }
  .back-url {
    position: absolute; left: 0; right: 0; top: 241px; text-align: center;
    font-family: "Didact Gothic", "Century Gothic", sans-serif;
    color: var(--light-text); font-size: 21px; letter-spacing: 1.5px;
  }
</style>
</head>
<body>
  <section class="card card-front" aria-label="Card front">
    <div class="brand"><span class="brand-mark"></span><span class="brand-name">ZANTOR</span></div>

    <ul class="contact-list">
      <li>
        <svg class="contact-icon" viewBox="0 0 12 12" aria-hidden="true"><circle cx="6" cy="6" r="6" fill="var(--brand-green)"/><path d="M3.6 3.2 L5 3 L5.5 4.6 L4.7 5.2 Q5.4 6.7 6.8 7.3 L7.4 6.5 L9 7 L8.8 8.4 Q5 8.6 3.6 3.2Z" fill="#fff"/></svg>
        <span>318.204.6637</span>
      </li>
      <li>
        <svg class="contact-icon" viewBox="0 0 12 12" aria-hidden="true"><circle cx="6" cy="6" r="6" fill="var(--brand-green)"/><rect x="3" y="4" width="6" height="4.2" fill="#fff"/><path d="M3 4 L6 6.3 L9 4" stroke="var(--brand-green)" stroke-width="0.8" fill="none"/></svg>
        <span>owen@zantorhq.com</span>
      </li>
      <li>
        <svg class="contact-icon" viewBox="0 0 12 12" aria-hidden="true"><circle cx="6" cy="6" r="6" fill="var(--brand-green)"/><path d="M1 6 H11 M6 0.5 V11.5 M2 3.5 H10 M2 8.5 H10" stroke="#fff" stroke-width="0.8"/><ellipse cx="6" cy="6" rx="2.4" ry="5.5" stroke="#fff" stroke-width="0.8" fill="none"/></svg>
        <span>www.zantorhq.com</span>
      </li>
    </ul>

    <svg class="footer-wave" viewBox="0 0 525 298" aria-hidden="true">
      <path d="M40 236 C140 225 230 232 330 250 C410 264 470 268 525 268" stroke="var(--brand-green)" stroke-width="4" fill="none"/>
      <path d="M0 248 C120 230 230 245 330 262 C420 276 480 280 525 282 L525 298 L0 298 Z" fill="var(--charcoal)"/>
    </svg>

    <p class="person"><span class="person-name">Owen Lasko,</span> <span class="person-title">President</span></p>
  </section>

  <section class="card card-back" aria-label="Card back">
    <div class="brand"><span class="brand-mark"></span><span class="brand-name">ZANTOR</span></div>
    <p class="back-url">www.zantorhq.com</p>
  </section>
</body>
</html>
```